New bussiness card, using company logo.
Lionel Brisk
Manager/Director
Brisk Property Developments
Po Box 5347
Thuringowa Central
Qld
0491 638 205
lionel@briskpropertydevelopments
eye catching, vibrant colours, professional

```html
<!DOCTYPE html>
<html lang="en">
<head>
<meta charset="utf-8">
<title>Brisk Property Developments – Business Cards</title>
<link rel="stylesheet" href="https://fonts.googleapis.com/css2?family=Source+Sans+3:wght@400;600;700&family=Exo+2:wght@400&display=swap">
<style>
  :root {
    --backdrop: #2f2b35;
    --white: #ffffff;
    --green: #6cb843;
    --green-light: #8dc63f;
    --red: #e0262e;
    --grey: #6d6e71;
    --ink: #333333;
  }
  * { margin: 0; padding: 0; box-sizing: border-box; }
  html, body { width: 1200px; height: 767px; overflow: hidden; }
  body {
    position: relative;
    background: var(--backdrop);
    font-family: "Source Sans 3", Arial, sans-serif;
  }
  .card {
    position: absolute;
    width: 532px;
    height: 304px;
    border-radius: 22px;
    overflow: hidden;
  }
  .card--contact { left: 43px; top: 45px; background: var(--white); }
  .card--logo-white { left: 617px; top: 49px; background: var(--white); }
  .card--logo-green { left: 46px; top: 398px; background: linear-gradient(135deg, var(--green) 0%, var(--green-light) 100%); }
  .card--logo-red { left: 633px; top: 405px; background: var(--red); }

  /* Contact card */
  .brand-small {
    position: absolute;
    left: 26px; top: 82px;
    width: 230px;
    font-weight: 700;
    font-size: 25px;
    line-height: 1.05;
    text-transform: uppercase;
    color: var(--red);
  }
  .divider {
    position: absolute;
    left: 262px; top: 52px;
    width: 1px; height: 116px;
    background: #c8c8c8;
  }
  .contact {
    position: absolute;
    left: 272px; top: 58px;
    color: var(--ink);
  }
  .contact__name { font-weight: 600; font-size: 21px; color: var(--green); line-height: 1; }
  .contact__role { font-size: 15px; color: var(--red); margin-top: 4px; }
  .contact__line { display: flex; align-items: center; gap: 7px; font-size: 14px; margin-top: 12px; }
  .contact__line--email { font-size: 12.5px; margin-top: 10px; }
  .contact__line svg { flex: none; }
  .wave { position: absolute; left: 0; top: 0; }
  .address {
    position: absolute;
    left: 42px; top: 255px;
    font-size: 14px;
    line-height: 18px;
    color: var(--white);
  }

  /* Logo cards */
  .brand-large {
    position: absolute;
    left: 0; right: 0; top: 92px;
    text-align: center;
    font-weight: 700;
    font-size: 40px;
    line-height: 1.05;
    text-transform: uppercase;
  }
  .card--logo-white .brand-large { color: var(--red); }
  .card--logo-green .brand-large,
  .card--logo-red .brand-large { color: var(--white); }
  .website {
    position: absolute;
    left: 0; right: 0;
    text-align: center;
    font-family: "Exo 2", Arial, sans-serif;
    font-size: 13px;
    letter-spacing: 2.6px;
  }
  .card--logo-white .website { top: 265px; color: var(--ink); }
  .website__domain { color: var(--red); }
  .card--logo-green .website { top: 253px; color: var(--white); }
  .card--logo-red .website { top: 253px; color: var(--white); }
</style>
</head>
<body>

  <section class="card card--contact">
    <div class="brand-small">Brisk Property Developments</div>
    <div class="divider"></div>
    <div class="contact">
      <p class="contact__name">Lionel Brisk</p>
      <p class="contact__role">Manager/Director</p>
      <p class="contact__line">
        <svg width="10" height="12" viewBox="0 0 10 12" aria-hidden="true"><path d="M2 0 L4 3 L3 4.5 C3.5 6.5 5 8 6.5 8.5 L8 7.5 L10 10 L8.5 12 C4 11 0.5 7 0 2.5 Z" fill="var(--green)"/></svg>
        0491 638 205
      </p>
      <p class="contact__line contact__line--email">
        <svg width="10" height="8" viewBox="0 0 10 8" aria-hidden="true"><rect width="10" height="8" fill="var(--green)"/><path d="M0 0 L5 4.5 L10 0" stroke="var(--white)" fill="none" stroke-width="1"/></svg>
        lionel@briskpropertydevelopments.com
      </p>
    </div>
    <svg class="wave" width="532" height="304" viewBox="0 0 532 304" aria-hidden="true">
      <path d="M0 248 C100 222 220 232 320 258 C410 282 480 268 532 244 L532 248 C480 274 410 288 320 264 C220 238 100 230 0 253 Z" fill="var(--red)"/>
      <path d="M0 258 C100 236 220 246 320 270 C410 292 480 278 532 256 L532 304 L0 304 Z" fill="var(--green)"/>
    </svg>
    <p class="address">Po Box 5347<br>Wattlebrook Central , Vic</p>
  </section>

  <section class="card card--logo-white">
    <div class="brand-large">Brisk Property<br>Developments</div>
    <p class="website">www.<span class="website__domain">briskpropertydevelopments</span>.com</p>
  </section>

  <section class="card card--logo-green">
    <div class="brand-large">Brisk Property<br>Developments</div>
    <p class="website">www.briskpropertydevelopments.com</p>
  </section>

  <section class="card card--logo-red">
    <div class="brand-large">Brisk Property<br>Developments</div>
    <p class="website">www.briskpropertydevelopments.com</p>
  </section>

</body>
</html>
```